Bold, Modern, Clean "Kestrelwaymassage.com" website

Why we stand out?
We are a male and female mobile massage team. Our names are Paul and Lina. 
Kestrel Way is a Alder Bay based mobile massage service. Our massage is offered to the community with a goal of facilitating balance within each individual. We specialize in integrated Pain management, and sports/medical massage therapy. Every client's first assessment is attended by our male and female massage therapist team. Depending on the goals identified for an individual determines which therapist will be assigned to provide treatment, if not both.

Our passion...
Here at Kestrel Way, we have a great passion for Postural Resoration and how it is integrated into an individual's Massage treatment. We pride ourselves in being natural facilitators of healing, which takes the ego of the therapist out of the client's healing process. We strive to deliver the best massage possible by including modalities such as Neuromuscular, Myofascial release, spontaneous muscle release, postural restoration, orthopedic, and medical massage.

Our education...

We are both Graduates of Venmora, school of massage therapy. We have continuing education in medical massage, myofacial release, trigger point therapy, postural restoration, anatomy, and spontaneous muscle release. Lina is also a Certified Yoga Instructor, which amplifies her experience with flexibility and strength as it pertains to each individual. Paul's passion is Massage, stretching, and strength training to encourage postural restoration and realignment.

Our rates-

Our rates are $75/ 60 minutes, $95/ 90 minutes, and $120/ 120 minutes.

Education-
Both Lina and I worked as behavioral health professionals that specialized in life skills mentoring for youth who had experienced different types of trauma. This led us both to want to help others in a different environment, where individuals can be empowered to take responsibility over their own healing. To us, massage is a type of manipulation physical therapy, that encourages healing on many levels.

Advice to any massage client-
The most important thing to 'us', as Licenced providers is to get you on to our table to show you our skills. But a good therapist never forgets that it's not about what we do for you, but what we can facilitate for you. Your health and healing has nothing to do with us. It is yours, not ours. Identify what your goals are with any Therapist, and know what the end looks like. Progress should be tangible, such as range of motion, and decreased pain.

Lina and Paul at Kestrel Way are awesome! I recently had open heart surgery, and Lina worked on me to increase my range of motion while helping with the pinched nerve from my arm being in the same position for so long during my surgery. My wife drives a lot for work, and Paul has helped decrease her neck and lower back pain immensely. They are seriously the best therapists I have ever worked with. I would recommend them to anyone who needs anything from stress relief to a medical massage treatment. They are professional, up beat, easy going, and always on time. And, I love that they meet us where ever we like! We did a staycation recently, where they came to our hotel to give us relaxation massages. Although usually they come to our home, where we focus on pain related issues. We will continue to work with them for a long, long time.

Target Market(s)

Mobile massage therapy clients

Industry/Entity Type

Massage Therapy

Coding

Coded - Design and coding required

Number of Pages Required

1 page

Font styles to use
Serif
Sans Serif

Requirements
Must have
• Please add or remove any information that would help the presentation of our website. Our logo is posted below, please include into the website.
• Please include a contact field that includes, kestrelwaymassage@fernmail.net,
• (206) 555-0148
• We have also included our own stock photos, as well as a photo of Paul and Lina. Please include a cropped photo of both massage therapists.

```html
<!DOCTYPE html>
<html lang="en">
<head>
<meta charset="utf-8">
<title>Kestrel Way Massage</title>
<link href="https://fonts.googleapis.com/css2?family=Open+Sans:wght@400;600;700;800&family=Roboto+Slab:wght@400;700&display=swap" rel="stylesheet">
<style>
:root{
  --navy:#1f3a6e;
  --nav:#24407a;
  --blue:#2f6fc3;
  --ink:#2a2f38;
  --muted:#6b7280;
  --light:#f2f3f5;
  --star:#f0a020;
  --footer:#3b3d41;
  --footer-dark:#2a2b2e;
  --white:#ffffff;
}
*{box-sizing:border-box;margin:0;padding:0}
html,body{width:667px;height:1200px;overflow:hidden;background:var(--white)}
body{font-family:"Open Sans",Arial,sans-serif;color:var(--ink);font-size:8px;line-height:1.45}
.page{width:667px;height:1200px;position:relative}

/* header */
.site-header{height:84px;display:flex;align-items:center;justify-content:space-between;padding:0 28px 0 52px}
.brand{display:flex;align-items:center;gap:10px}
.brand-mark{width:60px;height:60px;border-radius:50%;background:var(--navy)}
.brand-name{font-family:"Roboto Slab",Georgia,serif;font-weight:700;font-size:20px;color:var(--navy)}
.header-right{display:flex;align-items:center;gap:18px}
.call{display:flex;align-items:center;gap:6px}
.call svg{width:22px;height:22px}
.call small{display:block;font-size:7px;color:var(--muted)}
.call strong{font-size:11px;color:var(--navy)}
.social{display:flex;gap:5px}
.social span{width:17px;height:17px;border-radius:50%;background:var(--blue)}
.social span:nth-child(2){background:#3b9bd8}
.social span:nth-child(3){background:#1f5aa6}
.social span:nth-child(4){background:#c94b3c}
.social span:nth-child(5){background:#5a6b80}

/* nav */
.main-nav{height:28px;background:var(--nav);margin:0 52px;border-radius:3px 3px 0 0;display:flex;align-items:center;padding:0 8px}
.main-nav a{color:var(--white);text-decoration:none;font-size:8px;font-weight:600;letter-spacing:.3px;flex:1;text-align:center;white-space:nowrap}

/* hero */
.hero{height:343px;position:relative;background:linear-gradient(100deg,#8a7c70 0%,#c8b9a8 35%,#e7ddd0 60%,#b7a897 100%)}
.hero-copy{position:absolute;left:56px;top:92px;width:260px;color:var(--white)}
.hero-copy h1{font-size:23px;font-weight:800;letter-spacing:.4px;line-height:1.1;margin-bottom:6px}
.hero-copy p{font-size:8px;line-height:1.5;opacity:.95}
.btn{display:inline-block;background:var(--blue);color:var(--white);font-size:8px;font-weight:600;padding:7px 18px;border-radius:2px;text-decoration:none}
.hero-copy .btn{margin-top:16px}
.quick-contact{position:absolute;left:455px;top:33px;width:157px;background:rgba(45,62,100,.55);border-radius:3px;overflow:hidden}
.quick-contact h3{background:var(--navy);color:var(--white);font-size:10px;font-weight:700;padding:7px 10px;letter-spacing:.4px}
.quick-contact form{padding:10px 10px 12px}
.field{display:flex;align-items:center;gap:6px;background:var(--white);height:20px;border-radius:2px;margin-bottom:8px;padding:0 6px;font-size:7px;color:var(--muted)}
.field i{width:8px;height:8px;border-radius:50%;background:#9aa3b2;display:block}
.field.message{height:34px;align-items:flex-start;padding-top:6px}
.quick-contact .btn{margin-top:4px;padding:6px 12px}

/* welcome */
.welcome{height:135px;text-align:center;padding:22px 60px 0}
.welcome h2{font-size:17px;font-weight:800;color:var(--ink);letter-spacing:.3px;margin-bottom:8px}
.welcome p{font-size:7px;color:var(--muted);line-height:1.55}
.welcome .btn{margin-top:9px;padding:6px 14px}

/* services */
.services{height:275px;background:var(--light);padding-top:30px}
.section-title{text-align:center;font-size:16px;font-weight:800;color:var(--ink);letter-spacing:.3px}
.section-title::after{content:"";display:block;width:34px;height:2px;background:var(--blue);margin:6px auto 0}
.cards{display:flex;gap:22px;padding:16px 52px 0}
.card{flex:1;background:var(--white);box-shadow:0 1px 3px rgba(0,0,0,.08)}
.card-photo{height:78px}
.card:nth-child(1) .card-photo{background:linear-gradient(135deg,#d9c6b2,#8fa4b4)}
.card:nth-child(2) .card-photo{background:linear-gradient(135deg,#c9b39c,#e9ddd0)}
.card:nth-child(3) .card-photo{background:linear-gradient(135deg,#b49a86,#dfd0c2)}
.card-body{padding:6px 8px 8px}
.card h4{font-size:8px;font-weight:700;color:var(--ink);text-transform:uppercase;white-space:nowrap}
.card .price{font-size:7px;color:var(--blue);font-weight:600;margin:1px 0 3px}
.card p{font-size:6.5px;color:var(--muted);line-height:1.45}
.card .more{font-size:6.5px;color:var(--blue);font-weight:600;margin-top:3px;display:block}

/* reviews */
.reviews{height:200px;padding-top:32px}
.review-list{display:flex;gap:30px;padding:22px 52px 0}
.review{flex:1;display:flex;gap:12px}
.avatar{width:58px;height:58px;border-radius:50%;flex:none}
.review:nth-child(1) .avatar{background:radial-gradient(circle at 50% 40%,#c9a58a,#5b6f8c)}
.review:nth-child(2) .avatar{background:radial-gradient(circle at 50% 40%,#d4b49a,#8b7a6e)}
.review h5{font-size:10px;font-weight:800;color:var(--navy);text-transform:uppercase}
.stars{display:flex;align-items:center;gap:2px;margin:2px 0 4px}
.stars svg{width:8px;height:8px}
.stars em{font-style:normal;font-size:6.5px;color:var(--muted);margin-left:4px}
.review p{font-size:6.5px;color:var(--muted);line-height:1.45}
.review .author{font-size:7px;font-weight:700;color:var(--star);margin-top:4px;display:block}
.review .author small{display:block;color:var(--muted);font-weight:400;font-size:6px}

/* footer */
.site-footer{position:absolute;left:0;top:1062px;width:667px;height:138px;background:var(--footer);color:#d6d8dc}
.footer-cols{display:flex;padding:18px 52px 0;gap:12px;height:112px}
.footer-col{flex:1}
.footer-col h6{font-size:7.5px;font-weight:700;color:var(--white);margin-bottom:6px;letter-spacing:.3px}
.footer-col li{list-style:none;font-size:6.5px;line-height:1.9;color:#c2c5cb}
.footer-col li::before{content:"› ";color:#8a8f98}
.footer-col.contact li::before,.footer-col.follow li::before{content:""}
.footer-social{display:flex;gap:5px;margin-top:6px}
.footer-social span{width:15px;height:15px;border-radius:50%;background:#6c7079}
.copyright{height:26px;background:var(--footer-dark);font-size:6.5px;color:#9da1a8;text-align:center;line-height:26px}
</style>
</head>
<body>
<div class="page">

<header class="site-header">
  <div class="brand">
    <span class="brand-mark"></span>
    <span class="brand-name">Kestrel Way</span>
  </div>
  <div class="header-right">
    <div class="call">
      <svg viewBox="0 0 24 24"><circle cx="12" cy="12" r="11" fill="none" stroke="#1f3a6e" stroke-width="1.5"/><path d="M8.5 6.5l2 2-1.2 1.6c.7 1.6 2 2.9 3.6 3.6l1.6-1.2 2 2-1.5 1.8c-3.9-.4-7.9-4.4-8.3-8.3z" fill="#1f3a6e"/></svg>
      <div><small>Call us</small><strong>(206) 555-0148</strong></div>
    </div>
    <div class="social"><span></span><span></span><span></span><span></span><span></span></div>
  </div>
</header>

<nav class="main-nav">
  <a href="#">HOME</a><a href="#">ABOUT</a><a href="#">SERVICES</a><a href="#">FAQ</a><a href="#">OUR TEAM</a><a href="#">GALLERY</a><a href="#">NEWS</a><a href="#">CONTACT US</a>
</nav>

<section class="hero" role="img" aria-label="Therapist giving a back massage to a client lying on a massage table">
  <div class="hero-copy">
    <h1>KESTREL WAY MASSAGE</h1>
    <p>Mobile massage brought to your home or hotel by a trained therapist team focused on balance and lasting relief.</p>
    <a class="btn" href="#">Call to action</a>
  </div>
  <aside class="quick-contact">
    <h3>QUICK CONTACT</h3>
    <form>
      <div class="field"><i></i>Enter your name</div>
      <div class="field"><i></i>Email Address</div>
      <div class="field"><i></i>Website</div>
      <div class="field message"><i></i>Your Message</div>
      <a class="btn" href="#">Call to action</a>
    </form>
  </aside>
</section>

<section class="welcome">
  <h2>WELCOME TO KESTREL WAY MASSAGE</h2>
  <p>Our two-therapist mobile team travels to you, bringing calm, focused bodywork wherever you feel most at ease. We work toward lasting balance for every client, with a focus on pain relief, posture and recovery after sport or injury. Your first session begins with a joint assessment, and the goals we set together decide which therapist leads your care, or whether you will work with both of us.</p>
  <a class="btn" href="#">View more info</a>
</section>

<section class="services">
  <h2 class="section-title">OUR SERVICES</h2>
  <div class="cards">
    <article class="card">
      <div class="card-photo" role="img" aria-label="Therapist working on a client's shoulder"></div>
      <div class="card-body">
        <h4>Primus bonorum et malorum</h4>
        <div class="price">$75 / 60 minutes</div>
        <p>Integrated pain management that restores range of motion and eases tension, tailored to the goals set at your first visit.</p>
        <a class="more" href="#">Read More</a>
      </div>
    </article>
    <article class="card">
      <div class="card-photo" role="img" aria-label="Client receiving a neck and back massage"></div>
      <div class="card-body">
        <h4>Voluptatem accusantium dolo</h4>
        <div class="price">$95 / 90 minutes</div>
        <p>Sports and medical massage with myofascial release and trigger point work to support recovery and strength.</p>
        <a class="more" href="#">Read More</a>
      </div>
    </article>
    <article class="card">
      <div class="card-photo" role="img" aria-label="Therapist stretching a client's leg"></div>
      <div class="card-body">
        <h4>Voluptas sit aspernatur aut</h4>
        <div class="price">$120 / 120 minutes</div>
        <p>Postural restoration and assisted stretching that build flexibility, realignment and lasting comfort for daily life.</p>
        <a class="more" href="#">Read More</a>
      </div>
    </article>
  </div>
</section>

<section class="reviews">
  <h2 class="section-title">LATEST REVIEWS</h2>
  <div class="review-list">
    <article class="review">
      <div class="avatar" role="img" aria-label="Portrait of reviewer"></div>
      <div>
        <h5>Denouncing pleasure</h5>
        <div class="stars">
          <svg viewBox="0 0 10 10"><path d="M5 .5l1.3 3 3.2.2-2.5 2 .8 3.2L5 7.2 2.2 8.9 3 5.7.5 3.7l3.2-.2z" fill="#f0a020"/></svg>
          <svg viewBox="0 0 10 10"><path d="M5 .5l1.3 3 3.2.2-2.5 2 .8 3.2L5 7.2 2.2 8.9 3 5.7.5 3.7l3.2-.2z" fill="#f0a020"/></svg>
          <svg viewBox="0 0 10 10"><path d="M5 .5l1.3 3 3.2.2-2.5 2 .8 3.2L5 7.2 2.2 8.9 3 5.7.5 3.7l3.2-.2z" fill="#f0a020"/></svg>
          <svg viewBox="0 0 10 10"><path d="M5 .5l1.3 3 3.2.2-2.5 2 .8 3.2L5 7.2 2.2 8.9 3 5.7.5 3.7l3.2-.2z" fill="#f0a020"/></svg>
          <svg viewBox="0 0 10 10"><path d="M5 .5l1.3 3 3.2.2-2.5 2 .8 3.2L5 7.2 2.2 8.9 3 5.7.5 3.7l3.2-.2z" fill="#f0a020"/></svg>
          <em>156 Reviews</em>
        </div>
        <p>A wonderful team! After my surgery they helped restore my range of motion and eased my wife's neck and back pain as well.</p>
        <span class="author">Darcy T.<small>Alder Bay</small></span>
      </div>
    </article>
    <article class="review">
      <div class="avatar" role="img" aria-label="Portrait of reviewer"></div>
      <div>
        <h5>Praesentium voluptatum</h5>
        <div class="stars">
          <svg viewBox="0 0 10 10"><path d="M5 .5l1.3 3 3.2.2-2.5 2 .8 3.2L5 7.2 2.2 8.9 3 5.7.5 3.7l3.2-.2z" fill="#f0a020"/></svg>
          <svg viewBox="0 0 10 10"><path d="M5 .5l1.3 3 3.2.2-2.5 2 .8 3.2L5 7.2 2.2 8.9 3 5.7.5 3.7l3.2-.2z" fill="#f0a020"/></svg>
          <svg viewBox="0 0 10 10"><path d="M5 .5l1.3 3 3.2.2-2.5 2 .8 3.2L5 7.2 2.2 8.9 3 5.7.5 3.7l3.2-.2z" fill="#f0a020"/></svg>
          <svg viewBox="0 0 10 10"><path d="M5 .5l1.3 3 3.2.2-2.5 2 .8 3.2L5 7.2 2.2 8.9 3 5.7.5 3.7l3.2-.2z" fill="#f0a020"/></svg>
          <svg viewBox="0 0 10 10"><path d="M5 .5l1.3 3 3.2.2-2.5 2 .8 3.2L5 7.2 2.2 8.9 3 5.7.5 3.7l3.2-.2z" fill="#f0a020"/></svg>
          <em>156 Reviews</em>
        </div>
        <p>Professional, upbeat, easy going and always on time. They came to our hotel for a relaxing staycation massage we will never forget.</p>
        <span class="author">Marcus H.<small>Alder Bay</small></span>
      </div>
    </article>
  </div>
</section>

<footer class="site-footer">
  <div class="footer-cols">
    <div class="footer-col">
      <h6>RESOURCES</h6>
      <ul><li>Blog</li><li>Policies</li><li>Sitemap</li></ul>
    </div>
    <div class="footer-col">
      <h6>MORE</h6>
      <ul><li>Locations</li><li>Terms of Service</li><li>Legal Notice</li></ul>
    </div>
    <div class="footer-col">
      <h6>OPENING TIME</h6>
      <ul><li>Mon-Sat: 9:00am to 6:00pm</li><li>Sun: 11:00am to 4:00pm</li></ul>
    </div>
    <div class="footer-col contact">
      <h6>CONTACT US</h6>
      <ul><li>kestrelwaymassage@fernmail.net</li><li>Alder Bay</li><li>(206) 555-0148</li></ul>
    </div>
    <div class="footer-col follow">
      <h6>FOLLOW US</h6>
      <ul><li>Connect with our social media</li></ul>
      <div class="footer-social"><span></span><span></span><span></span><span></span></div>
    </div>
  </div>
  <div class="copyright">© 2024 Kestrelwaymassage.com. All rights reserved.</div>
</footer>

</div>
</body>
</html>
```